Business Card Design Project

We are a construction company in Orange County, CA. We need a two sided business card. We would like the back to be our logo with web URL. Front should included Name, title, address, phone, fax and email address.

our address is
627 West Dorrance Blvd, Suite 308
Anaheim, CA 92718

Our logo files are attached.

Construction

```html
<!DOCTYPE html>
<html lang="en">
<head>
<meta charset="utf-8">
<title>Norvel Business Card</title>
<link href="https://fonts.googleapis.com/css2?family=Open+Sans:wght@400;600;700;800&display=swap" rel="stylesheet">
<style>
  :root {
    --brand-blue: #124a7c;
    --ink: #3a3a3a;
    --paper: #ffffff;
    --backdrop: #e4e4e4;
    --swoosh-light: #d9d9d9;
    --swoosh-dark: #8e8e8e;
  }
  * { margin: 0; padding: 0; box-sizing: border-box; }
  html, body { width: 960px; height: 1200px; overflow: hidden; }
  body {
    background: var(--backdrop);
    font-family: "Open Sans", sans-serif;
    position: relative;
  }
  .card {
    position: absolute;
    width: 840px;
    height: 480px;
    border-radius: 28px;
    overflow: hidden;
  }
  .card-front { left: 62px; top: 83px; background: var(--paper); color: var(--ink); }
  .card-back { left: 55px; top: 645px; background: var(--brand-blue); color: var(--paper); }

  .wordmark {
    position: absolute;
    left: 0; right: 0;
    text-align: center;
    font-weight: 800;
    letter-spacing: 2px;
    line-height: 1;
  }
  .card-front .wordmark { top: 46px; font-size: 118px; color: var(--brand-blue); }
  .card-back .wordmark { top: 160px; font-size: 156px; color: var(--paper); }

  .person {
    position: absolute;
    top: 197px; left: 0; right: 0;
    text-align: center;
    font-size: 31px;
    font-weight: 600;
  }
  .person .title { font-size: 20px; }

  .contact {
    position: absolute;
    top: 274px; left: 0; right: 0;
    text-align: center;
    font-size: 19px;
    line-height: 31px;
  }
  .contact b { font-style: italic; font-weight: 700; }
  .contact .sep { margin: 0 6px; }

  .swoosh { position: absolute; left: 0; top: 0; }

  .address {
    position: absolute;
    top: 404px; left: 370px; width: 356px;
    text-align: center;
    font-size: 22px;
    line-height: 33px;
    color: var(--paper);
  }

  .web {
    position: absolute;
    top: 398px; left: 0; right: 0;
    text-align: center;
    font-size: 28px;
    font-weight: 700;
  }
</style>
</head>
<body>

<section class="card card-front">
  <div class="wordmark">NORVEL</div>
  <div class="person">Your Name, <span class="title">Designation</span></div>
  <div class="contact">
    <div><b>p</b> : 1-555-0147 <span class="sep">|</span> <b>f</b> : 1-555-0147</div>
    <div><b>e</b> : info@norvelbuild.com <span class="sep">|</span> <b>w</b> : www.norvelbuild.com</div>
  </div>
  <svg class="swoosh" width="840" height="480" viewBox="0 0 840 480" aria-hidden="true">
    <defs>
      <linearGradient id="swooshGrey" x1="0" y1="0" x2="1" y2="0">
        <stop offset="0" stop-color="var(--swoosh-dark)"/>
        <stop offset="1" stop-color="var(--swoosh-light)"/>
      </linearGradient>
    </defs>
    <path d="M0,420 C150,398 300,380 440,374 C300,384 150,418 10,466 L0,470 Z" fill="url(#swooshGrey)"/>
    <path d="M0,480 L16,476 C160,428 300,384 440,375 C600,370 760,388 840,416 L840,480 Z" fill="var(--brand-blue)"/>
  </svg>
  <div class="address">627 West Dorrance Blvd<br>Suite 308, Anaheim, CA 92718</div>
</section>

<section class="card card-back">
  <div class="wordmark">NORVEL</div>
  <div class="web">www.norvelbuild.com</div>
</section>

</body>
</html>
```